A four page bi-fold A4 brochure

The words and photos are attached. We want an innovative design using www.quietmeadowfunds.co.uk fonts, colours and themes and any pics which can enhance. The Copper Kite Property logo should also be used as it is a joint venture.

real estate, financial services

```html
<!DOCTYPE html>
<html lang="en">
<head>
<meta charset="utf-8">
<title>Property Investment and Sourcing Intensive Course – Brochure Spread</title>
<link href="https://fonts.googleapis.com/css2?family=Montserrat:ital,wght@0,400;0,500;0,600;0,700;0,800;0,900;1,600;1,700&display=swap" rel="stylesheet">
<style>
  :root{
    --backdrop:#233659;
    --paper:#ffffff;
    --navy:#1d2858;
    --ink:#1c1c24;
    --maroon:#7d1530;
    --red:#b0142e;
    --footer:#1f2b48;
    --photo-brick:#8a5a3c;
    --photo-green:#4f6a34;
    --photo-sky:#b9d3ea;
  }
  *{box-sizing:border-box;margin:0;padding:0}
  html,body{width:1200px;height:1200px;overflow:hidden;background:var(--backdrop)}
  body{font-family:"Montserrat",sans-serif;color:var(--ink);display:flex;align-items:center;justify-content:center}
  .spread{width:1160px;height:820px;display:flex;box-shadow:0 30px 60px rgba(0,0,0,.35)}
  .page{position:relative;width:580px;height:820px;background:var(--paper);padding:34px 30px 60px;overflow:hidden}
  .page--left{border-right:1px solid #e3e3e8}
  .page-footer{position:absolute;left:0;right:0;bottom:0;height:26px;background:var(--footer);border-top:5px solid var(--maroon)}
  .deal{display:flex;gap:14px;margin-bottom:16px}
  .deal__text{flex:1}
  .deal__title{font-weight:900;color:var(--navy);font-size:21px;letter-spacing:.5px;line-height:1.1;margin-bottom:6px}
  .deal__lead{font-size:10.5px;margin-bottom:6px}
  .deal__facts{border-left:3px solid var(--maroon);padding-left:9px;font-size:10.5px;line-height:1.35}
  .deal__facts p{margin-bottom:6px}
  .deal__facts strong{font-weight:800}
  .photo{flex:0 0 215px;height:130px;border-radius:2px}
  .photo--villa{background:linear-gradient(180deg,var(--photo-sky) 0%,var(--photo-brick) 45%,var(--photo-green) 100%)}
  .photo--terrace{background:linear-gradient(180deg,var(--photo-sky) 0%,#5b3a2c 40%,#e6e2d8 75%,#6c6a66 100%)}
  .pitch{font-size:10.5px;text-align:center;line-height:1.35;margin-bottom:8px}
  .pitch strong{display:block;font-weight:800}
  .headline{color:var(--red);font-weight:900;font-size:17px;line-height:1.2}
  .course-title{color:var(--navy);font-weight:800;font-size:18px;line-height:1.2;margin-bottom:2px}
  .objectives-title{text-align:center;font-weight:800;font-size:14px;margin-bottom:6px}
  .module{font-size:10.5px;line-height:1.4;margin-bottom:8px}
  .module__head{font-weight:800;margin-bottom:2px}
  .module ol{list-style:none}
  .module em{font-weight:700}
  .media-row{display:flex;justify-content:space-around;align-items:center;margin:10px 0 14px}
  .media{border-radius:3px}
  .media--book{width:120px;height:150px;background:linear-gradient(135deg,#1e3a34,#0f1d1a);box-shadow:4px 6px 10px rgba(0,0,0,.3)}
  .media--auction{width:200px;height:120px;background:linear-gradient(180deg,#f3f3f3 0%,#d8ecd0 30%,#ffffff 55%,#e2452f 85%)}
  .tags{display:flex;flex-wrap:wrap;gap:6px;justify-content:center;margin:8px 0 16px}
  .tag{background:var(--maroon);color:#fff;font-weight:700;font-size:9.5px;padding:3px 12px}
  .media-pair{display:flex;justify-content:space-between;align-items:flex-end;margin-top:12px}
  .media--bridging{width:200px;height:110px;background:linear-gradient(180deg,#fafafa,#e6dccb)}
  .media--mortgage{width:240px;height:130px;background:linear-gradient(135deg,#9fd0ee,#5fa6d6)}
</style>
</head>
<body>
<main class="spread">
  <section class="page page--left">
    <article class="deal">
      <div class="deal__text">
        <h2 class="deal__title">PROPERTY INVESTORS:</h2>
        <p class="deal__lead">We will show you how to source deals like this:</p>
        <div class="deal__facts">
          <p><strong>Apartment for £5,000 (purchased 2023)</strong></p>
          <p>In 2017, this property sold for £59,950. It could be resold now, in 2023, for up to as much as £85,000. It was purchased by us for £5,000 cash plus debt – an asset for debt swap. No refurbishment was required. Market rent is £550 pcm or £6,600.</p>
          <p><strong>Equity c. £60,000 Yield 44%</strong></p>
        </div>
      </div>
      <div class="photo photo--villa" role="img" aria-label="Red-brick Victorian apartment building behind a hedge"></div>
    </article>

    <article class="deal">
      <div class="deal__text">
        <h2 class="deal__title">PROPERTY SOURCING AGENTS &amp; INVESTORS:</h2>
        <p class="deal__lead">We will show you how to source deals like this:</p>
        <div class="deal__facts">
          <p><strong>House - £90,000 (purchased 2023)</strong></p>
          <p>28% below market value. Yield 10% or 17% net as a HMO.</p>
          <p>Fee earned £4,000 plus add-ons.</p>
          <p>The same client has purchased 5 properties this year, a minimum fee income of £20,000 before add-ons from just one client.</p>
        </div>
      </div>
      <div class="photo photo--terrace" role="img" aria-label="Row of terraced houses with bay windows"></div>
    </article>

    <p class="pitch"><strong>You can do this!</strong>Be a property investor AND property sourcing agent. The deals you have spent time researching and do not want, sell to others for a fee and also JV with agents to sell to their clients.</p>

    <h1 class="headline">LEARN HOW TO BUY PROPERTY AND FLIP, USING NO CASH!</h1>
    <h2 class="course-title">The Property Investment and Sourcing Intensive Course:</h2>
    <h3 class="objectives-title">Core objectives</h3>

    <div class="module">
      <p class="module__head">1. Distressed Property Investment – Source property substantially below market value (BMV)</p>
      <ol>
        <li>a. What is a distressed asset, and why now is the best time to invest since 2008/2009.</li>
        <li>b. How to source BMV distressed assets for personal investment purposes or to sell on to others, either for a fee or profit (flip).</li>
        <li>c. Buy properties with NO CASH and flip for profit using a professional legal technique.</li>
        <li>d. What's a property Call Option?</li>
        <li>e. Creating a viable property strategy, whether for investment, development, or sourcing.</li>
        <li>f. Houses v HMOs v Leasehold Flats – what's the best strategy in the current market?</li>
        <li>g. Learn to value a property like a professional.</li>
        <li>h. Understand the key investment ratios and numbers which make a potentially good investment, OUTSTANDING.</li>
      </ol>
    </div>
    <div class="page-footer"></div>
  </section>

  <section class="page page--right">
    <div class="module">
      <p class="module__head">2. Property Auctions – Repossessions, Bankruptcies and Bargain Properties LIVE</p>
      <ol>
        <li>i. <em>50% below market value (BMV) is achievable</em> – illustrated with real-world examples.</li>
        <li>j. Property Auctions – Not all properties at auction offer value. How to sort the outstanding opportunities from the duds.</li>
        <li>k. Property auction strategies and tactics that work in 2023.</li>
        <li>l. Navigate the legal pack – fix issues for a huge uplift in value – real-world examples.</li>
      </ol>
    </div>
    <div class="media-row">
      <div class="media media--book" role="img" aria-label="Cover of a guide book on property auctions"></div>
      <div class="media media--auction" role="img" aria-label="Online auction result screen showing a lot sold for £55,000"></div>
    </div>

    <div class="module">
      <p class="module__head">3. Off-market</p>
      <ol>
        <li>m. How to source off-market opportunities. 100% or more below market value (BMV) is achievable. Illustrated with real-world examples.</li>
        <li>n. Sources of Intelligence – Where do you find off-market bargains like this?</li>
      </ol>
    </div>
    <div class="tags">
      <span class="tag">Purchased 2023 - £17,500</span>
      <span class="tag">Sold in 2017 for £59,950</span>
      <span class="tag">Potential value £85,000</span>
      <span class="tag">2-bed garden flat - £5,000 refurbishment Yield 28%</span>
    </div>

    <div class="module">
      <p class="module__head">4. Law - how to fix problems for an instant uplift in equity</p>
      <ol>
        <li>o. The legal pitfalls to avoid and the legal challenges to embrace.</li>
        <li>p. Do you buy in a limited company or as an individual?</li>
        <li>q. How to manage risk. The risk management matrix.</li>
      </ol>
    </div>
    <div class="module">
      <p class="module__head">5. Finance – the latest bridging and mortgage advice</p>
      <ol>
        <li>r. Discover the best and most up-to-date sources of finance available. Get the latest mortgage and bridging advice from an expert, and also learn how to qualify.</li>
      </ol>
    </div>
    <div class="media-pair">
      <div class="media media--bridging" role="img" aria-label="Hand placing a coin beside stacked coins and a bridging loan house model"></div>
      <div class="media media--mortgage" role="img" aria-label="Model house beside a fixed rate versus variable rate mortgage sign"></div>
    </div>
    <div class="page-footer"></div>
  </section>
</main>
</body>
</html>
```